Business Card Design Project

This is to go hand in hand with our stationery project.
Target Market(s)
Business Professionals in the Finance, HR and C-Level management arena. They are global companies that run enterprise technology solutions/products.
Mostly Male, mid 30's to 60's.
Industry/Entity Type
Business
Font styles to use
Other font styles liked:
- Calibri
Colors
9bcb3c
000000
1b1b1b
c4c4c4
ffffff
Requirements
Must have
- Logo
Name, title, contact details, address on the front of the card.
ABN and web address need to be on the card, along with our tag line
See | Share | Do
We also require rounded corners and for the card to be landscape please.
Our green is
C98 M0 Y93 K0
Modern, contemporary and must have white space for people to write on.
Nice to have
- Consistent elements with the stationery design.
Should not have
- No 90's waves - We want the feeling of movement but no wavey lines.

```html
<!DOCTYPE html>
<html lang="en">
<head>
<meta charset="utf-8">
<title>Norvale Business Solutions – Business Cards</title>
<link href="https://fonts.googleapis.com/css2?family=Carlito:wght@400;700&display=swap" rel="stylesheet">
<style>
  :root {
    --green: #9bcb3c;
    --black: #000000;
    --charcoal: #1b1b1b;
    --grey: #c4c4c4;
    --white: #ffffff;
    --backdrop: #e9e6e2;
  }
  * { box-sizing: border-box; margin: 0; padding: 0; }
  html, body {
    width: 1200px; height: 914px; overflow: hidden;
    background: var(--backdrop);
    font-family: "Carlito", "Calibri", sans-serif;
  }
  .canvas {
    width: 1200px; height: 914px;
    display: flex; flex-direction: column; align-items: center; justify-content: center;
    gap: 28px;
  }
  .card {
    position: relative;
    width: 680px; height: 415px;
    background: var(--black);
    border-radius: 10px;
    box-shadow: 0 8px 22px rgba(0,0,0,.22);
    overflow: hidden;
  }

  /* brand lockup */
  .brand { position: absolute; display: flex; flex-direction: column; }
  .brand-mark { display: flex; align-items: center; gap: 10px; }
  .brand-name {
    color: var(--white); font-weight: 700; font-size: 48px; line-height: 1;
    letter-spacing: 1px;
  }
  .brand-dot { width: 15px; height: 15px; border-radius: 50%; background: var(--green); }
  .brand-sub { color: var(--white); font-weight: 700; font-size: 15px; margin-top: 6px; }

  /* front */
  .card-front .brand { left: 56px; top: 100px; }
  .divider {
    position: absolute; left: 290px; top: 62px; width: 3px; height: 290px;
    background: var(--green);
  }
  .details { position: absolute; left: 326px; top: 74px; right: 18px; }
  .company {
    color: var(--white); font-weight: 700; font-size: 26px; line-height: 1.05;
    white-space: nowrap;
  }
  .abn { color: var(--green); font-size: 19px; margin-top: 2px; }
  .contact-list { list-style: none; margin-top: 24px; }
  .contact-list li {
    display: flex; align-items: flex-start; gap: 18px;
    color: var(--green); font-size: 19px; line-height: 1.15; margin-bottom: 9px;
  }
  .contact-list svg { flex: 0 0 20px; width: 20px; height: 20px; fill: var(--white); margin-top: 1px; }

  /* back */
  .card-back .brand { right: 60px; top: 196px; align-items: flex-start; }
  .tagline {
    position: absolute; right: 60px; top: 290px;
    display: flex; align-items: center; gap: 24px;
    color: var(--green); font-size: 22px;
  }
  .tagline .sep { width: 2px; height: 26px; background: var(--white); transform: skewX(-18deg); }
  .card-back .abn { position: absolute; right: 60px; top: 334px; font-size: 21px; margin: 0; }
</style>
</head>
<body>
<main class="canvas">

  <section class="card card-front" aria-label="Business card front">
    <div class="brand">
      <div class="brand-mark">
        <span class="brand-name">Norvale</span>
        <span class="brand-dot"></span>
      </div>
      <span class="brand-sub">Norvale Business Solutions</span>
    </div>

    <div class="divider"></div>

    <div class="details">
      <h1 class="company">Norvale Business Solutions</h1>
      <p class="abn">ABN: 48 213 770 915</p>
      <ul class="contact-list">
        <li>
          <svg viewBox="0 0 24 24" aria-label="Phone"><path d="M6.6 10.8a15.1 15.1 0 0 0 6.6 6.6l2.2-2.2c.3-.3.7-.4 1-.2 1.1.4 2.3.6 3.6.6.6 0 1 .4 1 1V20c0 .6-.4 1-1 1C10.6 21 3 13.4 3 4c0-.6.4-1 1-1h3.5c.6 0 1 .4 1 1 0 1.3.2 2.5.6 3.6.1.3 0 .7-.2 1z"/></svg>
          <span>+61 2 9000 4817</span>
        </li>
        <li>
          <svg viewBox="0 0 24 24" aria-label="Fax"><path d="M7 3h8l2 2v4H7z M4 10h16a1 1 0 0 1 1 1v7a1 1 0 0 1-1 1h-3v2H7v-2H4a1 1 0 0 1-1-1v-7a1 1 0 0 1 1-1zm5 6v3h6v-3z"/></svg>
          <span>+61 2 9000 5926</span>
        </li>
        <li>
          <svg viewBox="0 0 24 24" aria-label="Address"><path d="M12 2a7 7 0 0 0-7 7c0 5.2 7 13 7 13s7-7.8 7-13a7 7 0 0 0-7-7zm0 9.5A2.5 2.5 0 1 1 12 6.5a2.5 2.5 0 0 1 0 5z"/></svg>
          <span>Level 4, 27 Harbour Lane,<br>Northbridge NSW 2063</span>
        </li>
        <li>
          <svg viewBox="0 0 24 24" aria-label="Email"><path d="M3 5h18v14H3zm2 2v.4l7 4.6 7-4.6V7zm0 2.8V17h14V9.8l-7 4.6z"/></svg>
          <span>Sales@norvalebiz.com</span>
        </li>
        <li>
          <svg viewBox="0 0 24 24" aria-label="Website"><path d="M12 2a10 10 0 1 0 0 20 10 10 0 0 0 0-20zm6.9 6h-3a15 15 0 0 0-1.3-3.9A8 8 0 0 1 18.9 8zM12 4c.9 1.2 1.6 2.5 2 4h-4c.4-1.5 1.1-2.8 2-4zM4.3 14a8 8 0 0 1 0-4h3.3a16 16 0 0 0 0 4zm.8 2h3a15 15 0 0 0 1.3 3.9A8 8 0 0 1 5.1 16zM8.1 8h-3a8 8 0 0 1 4.3-3.9A15 15 0 0 0 8.1 8zM12 20c-.9-1.2-1.6-2.5-2-4h4c-.4 1.5-1.1 2.8-2 4zm2.3-6H9.7a14 14 0 0 1 0-4h4.6a14 14 0 0 1 0 4zm.3 5.9A15 15 0 0 0 15.9 16h3a8 8 0 0 1-4.3 3.9zm1.8-5.9a16 16 0 0 0 0-4h3.3a8 8 0 0 1 0 4z"/></svg>
          <span>www.norvalebiz.com</span>
        </li>
      </ul>
    </div>
  </section>

  <section class="card card-back" aria-label="Business card back">
    <div class="brand">
      <div class="brand-mark">
        <span class="brand-name">Norvale</span>
        <span class="brand-dot"></span>
      </div>
      <span class="brand-sub">Norvale Business Solutions</span>
    </div>
    <div class="tagline">
      <span>Plan</span><span class="sep"></span>
      <span>Build</span><span class="sep"></span>
      <span>Grow</span>
    </div>
    <p class="abn">ABN: 48 213 770 915</p>
  </section>

</main>
</body>
</html>
```